Eyecatching website design for commercial lighting business

This contest is all about the graphic design aspect. We need a striking website design for a commercial lighting company. We want something really eye catching to introduce people to our range of induction and LED lights which save businesses money on maintenance and electricity costs.

To be successful in this contest you will need to provide a design and pictures for the pages listed below.

We are using the platform velbrin.com.au and you can see the attached template which everything will be loaded into so we just need HTML files which we can upload and we can do everything else from Velbrin.

The final design should be strong and clean and use the colours and textures in the attached business card file.

Detailed requirements:

Please see attached screenshot of the website template, all we need is a fantastic graphic design and improvement/ incorporation of our logo for the following pages
Page Headings:
1. Home
About Us, Contact Us, snapshot of and link to Blog

Each of the below pages will have several paragraphs of text followed by a list of suitable products which is generated from our product catalogue.

2. Car Park Lighting
3. Educational Lighting
4. Hospitality Lighting
5. Office & Shop Lighting
6. Warehouse Lighting

Some of the website we have seen which are similar in nature are:
http://www.quorvanlamps.com.au/
http://www.tibrox.com/
http://www.gandowlumen.net/commercial-led
but we really want a modern, eye catching and memorable design

Some of the designs built on Velbrin that we like are:

http://www.pemberhollow.com.au/
http://www.marwickgoods.com.au/
http://www.kelmorabay.com.au/

I've also uploaded a couple of photos that we love. We'd like something similar for each industry.

Target Market(s)

Company Owners, Maintenance & Facilities Managers, Electrical Contractors

Industry/Entity Type

Electrical

Coding

Coded - Design and coding required

Number of Pages Required

5+ page

Font styles to use
Sans Serif

Colors
33a6d7
ec1f27

Requirements
Must have
• -Must scale to mobile
• -HTML coded files need to be provided (HTML Bootstrap)
Nice to have
• -Prefer incorporation of our logo into header bar
• -Design of 2-3 advertising banners which can be displayed on the home page
• -Prominent call to action button towards top of page 'Get a quote' or similar
• -Grid based design HTML Bootstrap

```html
<!DOCTYPE html>
<html lang="en">
<head>
<meta charset="utf-8">
<title>Halvern Business Solutions – Commercial Lighting</title>
<link href="https://fonts.googleapis.com/css2?family=Open+Sans:wght@400;600;700;800&display=swap" rel="stylesheet">
<style>
:root{
  --blue:#33a6d7;
  --blue-dark:#1f86b8;
  --blue-deep:#176f9a;
  --red:#ec1f27;
  --ink:#333;
  --muted:#777;
  --line:#e4e4e4;
  --bg:#ffffff;
}
*{box-sizing:border-box;margin:0;padding:0}
html,body{width:706px;height:1200px;overflow:hidden;background:var(--bg)}
body{font-family:"Open Sans",Arial,sans-serif;color:var(--ink);position:relative}
.wrap{position:absolute;left:78px;width:550px}

/* header */
.site-header{position:absolute;top:0;left:0;width:706px;height:78px}
.brand{position:absolute;left:78px;top:16px;display:flex;align-items:center;gap:8px}
.brand-mark{width:34px;height:34px;background:var(--red)}
.brand-name{font-size:15px;font-weight:800;color:var(--red);line-height:1.05;text-transform:uppercase;width:150px}
.header-contact{position:absolute;right:78px;top:20px;text-align:right}
.header-contact .tag{font-size:8px;color:var(--muted);letter-spacing:.5px;text-transform:uppercase}
.header-contact .phone{font-size:17px;font-weight:700;color:var(--red);display:flex;align-items:center;gap:5px;justify-content:flex-end;margin-top:2px}

/* nav */
.main-nav{position:absolute;top:78px;left:0;width:706px;height:25px;background:var(--blue)}
.main-nav ul{position:absolute;left:78px;width:550px;height:25px;list-style:none;display:flex}
.main-nav li{font-size:8px;font-weight:700;color:#fff;padding:0 17px;line-height:25px;text-transform:uppercase}
.main-nav li.active{background:var(--blue-dark)}
.main-nav .search{margin-left:auto;padding:0 12px;background:var(--blue-dark);display:flex;align-items:center}

/* hero */
.hero{position:absolute;top:103px;left:0;width:706px;height:297px;background:linear-gradient(180deg,#c7d4dc 0%,#93a4ae 35%,#8a7560 70%,#5b4a3b 100%)}
.hero-title{position:absolute;left:130px;top:118px;font-size:25px;font-weight:800;color:#fff;line-height:1.05;text-transform:uppercase}
.hero-btn{position:absolute;left:130px;top:178px;background:var(--blue-deep);color:#fff;font-size:8px;font-weight:700;padding:8px 16px;letter-spacing:.5px}
.hero-arrow{position:absolute;top:135px;width:22px;height:22px;background:rgba(0,0,0,.35);display:flex;align-items:center;justify-content:center}
.hero-arrow.prev{left:0}.hero-arrow.next{right:0}
.hero-dots{position:absolute;top:276px;left:323px;display:flex;gap:6px}
.hero-dots i{width:7px;height:7px;border-radius:50%;background:#fff;opacity:.7}
.hero-dots i.on{opacity:1;background:var(--blue)}

/* headings */
.section-title{font-size:12px;font-weight:700;text-transform:uppercase;color:var(--red)}
.section-title span{color:var(--blue)}
.section-title::after{content:"";display:block;width:26px;height:2px;background:var(--red);margin-top:4px}

/* solutions */
.solutions{top:420px}
.tiles{position:absolute;top:447px;left:78px;width:550px;display:flex;gap:6px}
.tile{flex:1;height:113px;position:relative}
.tile .photo{position:absolute;inset:0 0 24px 0}
.tile .caption{position:absolute;left:0;right:0;bottom:0;height:24px;background:var(--blue);color:#fff;font-size:7px;font-weight:700;line-height:24px;padding-left:8px;text-transform:uppercase}

/* feature */
.feature-video{position:absolute;left:78px;top:572px;width:322px;height:204px;background:radial-gradient(circle at 50% 45%,#f7e7a8 0%,#c99a3a 35%,#3a2a16 80%)}
.play{position:absolute;left:142px;top:82px;width:38px;height:28px;border-radius:6px;background:var(--red);display:flex;align-items:center;justify-content:center}
.video-caption{position:absolute;left:0;bottom:0;width:100%;background:rgba(0,0,0,.55);color:#fff;font-size:7px;padding:6px 10px}
.feature-box{position:absolute;left:405px;top:572px;width:223px;height:204px;background:var(--blue);color:#fff;padding:22px 16px;text-align:center}
.feature-box h3{font-size:9px;font-weight:700;line-height:1.4}
.feature-box p{font-size:7px;line-height:1.6;margin-top:10px;opacity:.95}
.btn-red{display:inline-block;background:var(--red);color:#fff;font-size:7px;font-weight:700;padding:6px 12px;margin-top:14px;text-transform:uppercase}

/* blog */
.blog{top:804px}
.posts{position:absolute;top:835px;left:78px;width:550px;display:flex;gap:22px}
.post{flex:1;display:flex;gap:8px}
.post-icon{width:16px;height:16px;border-radius:50%;background:var(--red);flex:none;margin-top:2px}
.post .date{font-size:6.5px;color:var(--muted)}
.post h4{font-size:8.5px;font-weight:700;line-height:1.3;margin-top:3px}
.post p{font-size:6.5px;color:var(--muted);line-height:1.6;margin-top:5px}
.post .more{font-size:7px;font-weight:700;color:var(--red);margin-top:7px;text-transform:uppercase}

/* footer */
.site-footer{position:absolute;top:988px;left:0;width:706px;height:187px;background:var(--blue);color:#fff}
.footer-cols{position:absolute;left:78px;top:18px;width:550px;display:flex;gap:18px}
.footer-col h5{font-size:8.5px;font-weight:700;margin-bottom:12px}
.footer-col{font-size:6.5px;line-height:1.7}
.col-contact{width:130px}.col-news{width:70px}.col-follow{width:100px}.col-news-sub{flex:1}
.contact-row{display:flex;gap:6px;margin-bottom:7px;align-items:flex-start}
.socials{display:flex;gap:5px}
.socials i{width:16px;height:16px;border-radius:50%;background:var(--blue-deep);display:block}
.socials i:last-child{background:var(--red)}
.subscribe-input{margin-top:10px;background:#fff;color:var(--muted);height:20px;font-size:7px;line-height:20px;padding-left:8px;width:120px}
.subscribe-btn{margin-top:8px;background:var(--blue-deep);color:#fff;height:22px;width:120px;text-align:center;font-size:7.5px;font-weight:700;line-height:22px;text-transform:uppercase}
.copyright{position:absolute;left:78px;top:163px;font-size:6.5px}
.footer-base{position:absolute;top:1175px;left:0;width:706px;height:25px;background:var(--blue-deep)}
</style>
</head>
<body>

<header class="site-header">
  <div class="brand">
    <div class="brand-mark"></div>
    <div class="brand-name">Halvern Business Solutions</div>
  </div>
  <div class="header-contact">
    <div class="tag">Contact us and save money</div>
    <div class="phone">
      <svg width="13" height="13" viewBox="0 0 24 24"><path fill="#ec1f27" d="M6.6 10.8a15 15 0 0 0 6.6 6.6l2.2-2.2c.3-.3.7-.4 1-.2 1.1.4 2.3.6 3.6.6.6 0 1 .4 1 1V20c0 .6-.4 1-1 1A17 17 0 0 1 3 4c0-.6.4-1 1-1h3.5c.6 0 1 .4 1 1 0 1.3.2 2.5.6 3.6.1.3 0 .7-.2 1z"/></svg>
      (513) 4270.316
    </div>
  </div>
</header>

<nav class="main-nav">
  <ul>
    <li class="active">Home</li><li>About us</li><li>Products</li><li>Blog</li><li>Contact us</li>
    <li class="search"><svg width="9" height="9" viewBox="0 0 24 24"><circle cx="10" cy="10" r="7" fill="none" stroke="#fff" stroke-width="3"/><path d="M15 15l7 7" stroke="#fff" stroke-width="3"/></svg></li>
  </ul>
</nav>

<section class="hero" role="img" aria-label="Warehouse aisle with tall stacked shelving lit by bright ceiling lights">
  <h1 class="hero-title">Warehouse<br>Lighting</h1>
  <div class="hero-btn">LEARN MORE ›</div>
  <div class="hero-arrow prev"><svg width="8" height="10" viewBox="0 0 8 10"><path d="M6 1L2 5l4 4" stroke="#fff" stroke-width="1.6" fill="none"/></svg></div>
  <div class="hero-arrow next"><svg width="8" height="10" viewBox="0 0 8 10"><path d="M2 1l4 4-4 4" stroke="#fff" stroke-width="1.6" fill="none"/></svg></div>
  <div class="hero-dots"><i></i><i class="on"></i><i></i><i></i><i></i></div>
</section>

<h2 class="wrap section-title solutions">Lighting <span>Solutions</span></h2>
<div class="tiles">
  <div class="tile"><div class="photo" role="img" aria-label="Car park with overhead lights" style="background:linear-gradient(#d9dde0,#8f979c)"></div><div class="caption">Car park lighting ›</div></div>
  <div class="tile"><div class="photo" role="img" aria-label="Lit classroom interior" style="background:linear-gradient(#e7dfcf,#a08d6d)"></div><div class="caption">Educational lighting ›</div></div>
  <div class="tile"><div class="photo" role="img" aria-label="Hotel lobby with warm lighting" style="background:linear-gradient(#f0e7d8,#b69a78)"></div><div class="caption">Hospitality lighting ›</div></div>
  <div class="tile"><div class="photo" role="img" aria-label="Open plan office with ceiling panels" style="background:linear-gradient(#e6ecef,#9aa7ad)"></div><div class="caption">Office lighting ›</div></div>
</div>

<div class="feature-video" role="img" aria-label="Close up of glowing LED light array">
  <div class="play"><svg width="12" height="12" viewBox="0 0 12 12"><path d="M3 1l8 5-8 5z" fill="#fff"/></svg></div>
  <div class="video-caption">Contrary to popular belief, Lorem Ipsum</div>
</div>
<div class="feature-box">
  <h3>Welcome to the Commercial Lighting Division of Halvern Business Solutions</h3>
  <p>Retrofitting the lighting in a commercial or industrial premises is a great way to save money on energy costs and maintenance, create a safer work environment and reduce the load on the energy in the premises.</p>
  <div class="btn-red">Read more</div>
</div>

<h2 class="wrap section-title blog">Latest <span>Blog</span></h2>
<div class="posts">
  <article class="post"><div class="post-icon"></div><div>
    <div class="date">Posted on Aug 08, 2015</div>
    <h4>There are many variations of passages of Lorem Ipsum</h4>
    <p>Contrary to popular belief, Lorem Ipsum is not simply random text. It has roots in a piece of classical Latin literature from 45 BC, making it over 2000 years.</p>
    <div class="more">Read more ›</div></div></article>
  <article class="post"><div class="post-icon"></div><div>
    <div class="date">Posted on Aug 12, 2015</div>
    <h4>Contrary to popular belief, Lorem Ipsum is not simply</h4>
    <p>Into popular during the Renaissance. The first line of Lorem Ipsum comes from a line in section 1.10.32, since then it is loved.</p>
    <div class="more">Read more ›</div></div></article>
  <article class="post"><div class="post-icon"></div><div>
    <div class="date">Posted on Aug 20, 2015</div>
    <h4>But I must explain to you how all this mistaken idea of denouncing</h4>
    <p>No one rejects or avoids pleasure itself, because it is pleasure, but because those who do not know how to pursue it.</p>
    <div class="more">Read more ›</div></div></article>
</div>

<footer class="site-footer">
  <div class="footer-cols">
    <div class="footer-col col-contact">
      <h5>Contact us</h5>
      <div class="contact-row"><svg width="8" height="10" viewBox="0 0 24 30"><path fill="#fff" d="M12 0a10 10 0 0 0-10 10c0 8 10 20 10 20s10-12 10-20A10 10 0 0 0 12 0zm0 14a4 4 0 1 1 0-8 4 4 0 0 1 0 8z"/></svg><span>48 Tarrow Lane<br>Brenfield, VIC 3182</span></div>
      <div class="contact-row"><svg width="8" height="8" viewBox="0 0 24 24"><path fill="#fff" d="M6.6 10.8a15 15 0 0 0 6.6 6.6l2.2-2.2c.3-.3.7-.4 1-.2 1.1.4 2.3.6 3.6.6.6 0 1 .4 1 1V20c0 .6-.4 1-1 1A17 17 0 0 1 3 4c0-.6.4-1 1-1h3.5c.6 0 1 .4 1 1 0 1.3.2 2.5.6 3.6.1.3 0 .7-.2 1z"/></svg><span>T: (513) 4270.316</span></div>
      <div class="contact-row"><svg width="9" height="7" viewBox="0 0 24 18"><rect x="1" y="1" width="22" height="16" fill="none" stroke="#fff" stroke-width="2"/><path d="M1 1l11 9 11-9" fill="none" stroke="#fff" stroke-width="2"/></svg><span>hello@halvern.com.au</span></div>
    </div>
    <div class="footer-col col-news">
      <h5>News</h5>
      <div>Home</div><div>About us</div><div>Products</div><div>Blog</div><div>Contact us</div>
    </div>
    <div class="footer-col col-follow">
      <h5>Follow us on</h5>
      <div class="socials"><i></i><i></i><i></i><i></i></div>
    </div>
    <div class="footer-col col-news-sub">
      <h5>Newsletter Subscribe</h5>
      <div>Enter your email below to receive our monthly lighting newsletter.</div>
      <div class="subscribe-input">Email Id</div>
      <div class="subscribe-btn">Sign up!</div>
    </div>
  </div>
  <div class="copyright">Copyright © 2015 All Rights Reserved</div>
</footer>
<div class="footer-base"></div>

</body>
</html>
```